Awesome business card design needed

We need a new business card design to go with our new logo.
We are a web development agency that specialises in highly complex back-end integrations as opposed to design, our customers are retailers, hotels, hospitals and any other organisation that has a large online marketing department.
Take a look at our website - www.brenoloft.com for some inspiration.
We want our new business cards to exude class, professionalism and style.
We are likely to choose a high-end card to print them on but we want the design of the card itself to really turn heads.
We have no specific colour requirements, the logo as you will see is a turquoise colour R89 G171 B167 #59aba7 but it can also be in white if you want to make the colour of the card something different.
The information on the card should be:
Name
Position
Tel
email
Potentially a double sided card could have our web address, twitter and FB links.

```html
<!DOCTYPE html>
<html lang="en">
<head>
<meta charset="UTF-8">
<title>Brenoloft Business Card</title>
<link href="https://fonts.googleapis.com/css2?family=Jost:wght@400;500;700&display=swap" rel="stylesheet">
<style>
  :root {
    --teal: #59aba7;
    --white: #ffffff;
    --ink: #4a4a4a;
    --rule: #b9b9b9;
    --swoosh: #4f4f4f;
    --backdrop: #e4e5e7;
  }
  * { box-sizing: border-box; margin: 0; padding: 0; }
  html, body {
    width: 1200px; height: 987px; overflow: hidden;
    background: var(--backdrop);
    font-family: "Jost", "Futura", sans-serif;
  }
  .sheet {
    position: relative; width: 1200px; height: 987px;
    display: flex; align-items: center; justify-content: center; gap: 40px;
  }
  .card {
    position: relative; width: 540px; height: 310px;
    border-radius: 22px; overflow: hidden;
    box-shadow: 0 4px 14px rgba(0,0,0,0.12);
  }

  /* Front */
  .card-front { background: var(--white); }
  .card-front .swoosh { position: absolute; inset: 0; width: 100%; height: 100%; }
  .card-front .wordmark {
    position: absolute; left: 34px; top: 48px;
    font-size: 50px; font-weight: 700; color: var(--teal); letter-spacing: 1px;
  }
  .card-front .divider {
    position: absolute; left: 282px; top: 36px; width: 1px; height: 140px;
    background: var(--rule);
  }
  .identity { position: absolute; left: 304px; top: 36px; }
  .identity .name { font-size: 22px; font-weight: 700; color: var(--teal); line-height: 1.05; }
  .identity .position { font-size: 14px; color: var(--ink); }
  .contacts { position: absolute; left: 304px; top: 98px; list-style: none; }
  .contacts li {
    display: flex; align-items: center; gap: 9px;
    font-size: 16px; color: var(--ink); line-height: 26px;
  }
  .contacts svg { width: 13px; height: 13px; flex: none; }
  .address {
    position: absolute; right: 140px; bottom: 14px; text-align: right;
    color: var(--white); font-size: 14px; line-height: 1.3;
  }

  /* Back */
  .card-back { background: var(--teal); color: var(--white); }
  .card-back .wordmark {
    position: absolute; left: 0; right: 0; top: 72px; text-align: center;
    font-size: 86px; font-weight: 700; letter-spacing: 2px;
  }
  .follow {
    position: absolute; left: 0; right: 0; top: 196px;
    display: flex; justify-content: center; align-items: center; gap: 10px;
    font-size: 15px;
  }
  .follow .social { width: 24px; height: 24px; border-radius: 5px; background: var(--white); opacity: 0.9; }
  .card-back .web {
    position: absolute; left: 0; right: 0; top: 236px; text-align: center;
    font-size: 15px; letter-spacing: 1px;
  }
</style>
</head>
<body>
<main class="sheet">
  <section class="card card-front" aria-label="Card front">
    <svg class="swoosh" viewBox="0 0 540 310" preserveAspectRatio="none" aria-hidden="true">
      <path d="M0 160 C 150 195, 330 218, 420 248 C 460 262, 485 288, 500 310 L 0 310 Z" fill="var(--teal)"/>
      <path d="M30 172 C 170 196, 330 216, 420 248 C 455 262, 478 284, 488 310" fill="none" stroke="var(--white)" stroke-width="7"/>
      <path d="M30 178 C 170 202, 330 222, 420 254 C 455 268, 478 290, 488 310" fill="none" stroke="var(--swoosh)" stroke-width="4"/>
    </svg>
    <div class="wordmark">brenoloft</div>
    <div class="divider"></div>
    <div class="identity">
      <p class="name">Your Name</p>
      <p class="position">Position</p>
    </div>
    <ul class="contacts">
      <li>
        <svg viewBox="0 0 16 16"><circle cx="8" cy="8" r="7.5" fill="none" stroke="var(--teal)" stroke-width="1.2"/><path d="M5.5 4.5 L7 6 L6 7.2 C6.6 8.5 7.5 9.4 8.8 10 L10 9 L11.5 10.5 L10.5 11.8 C7.5 11.5 4.5 8.5 4.2 5.5 Z" fill="var(--teal)"/></svg>
        123-456-7890
      </li>
      <li>
        <svg viewBox="0 0 16 16"><rect x="1.5" y="4" width="13" height="9" rx="1.5" fill="var(--teal)"/><path d="M1.5 5 L8 9.5 L14.5 5" fill="none" stroke="var(--white)" stroke-width="1.2"/></svg>
        info@brenoloft.com
      </li>
      <li>
        <svg viewBox="0 0 16 16"><circle cx="8" cy="8" r="7" fill="var(--teal)"/><path d="M1 8 H15 M8 1 V15 M3 4 H13 M3 12 H13" stroke="var(--white)" stroke-width="0.8" fill="none"/><ellipse cx="8" cy="8" rx="3" ry="7" fill="none" stroke="var(--white)" stroke-width="0.8"/></svg>
        www.brenoloft.com
      </li>
    </ul>
    <p class="address">Street Name, City Name<br>State Zip Code</p>
  </section>

  <section class="card card-back" aria-label="Card back">
    <div class="wordmark">brenoloft</div>
    <div class="follow">
      <span>Follow Us On:</span>
      <span class="social" role="img" aria-label="Social network link"></span>
      <span class="social" role="img" aria-label="Social network link"></span>
    </div>
    <p class="web">www.brenoloft.com</p>
  </section>
</main>
</body>
</html>
```